Business card for my new company (Accounting firm)

I need a business card for my new business Brightwell Advisory and Ledger SA. Our services are accounting, tax, audit and financial management. Our customers are small companies, start-ups and new companies. The final design has to show financial security, trust and growth. Please find our logo attached to the business card. Text for the business card: Brightwell Advisory and Ledger SA Tomas Varenholt Director and Founder Certified Accountant Tel. 022 418 57 34 tv@clairevalconseil.ch www.clairevalconseil.ch Rue des Vergières 27 1201 Geneva
Target Market(s)
Our customers are small companies, start-ups and new companies.
Industry/Entity Type
Finance And Accounting
Contact Information for Business Card
Claireval Conseil et Comptes SA
Tomas Varenholt
Directeur et Fondateur
Expert-comptable diplômé
Tél. 022 418 57 34
tv@clairevalconseil.ch
www.clairevalconseil.ch
Rue des Vergières 27
1201 Genève

```html
<!DOCTYPE html>
<html lang="fr">
<head>
<meta charset="utf-8">
<title>Claireval Conseil et Comptes SA — Cartes de visite</title>
<link rel="stylesheet" href="https://fonts.googleapis.com/css2?family=Roboto:wght@300;400;500;700&display=swap">
<style>
  :root {
    --bg: #2b2b2d;
    --card: #ffffff;
    --edge: #1c679f;
    --accent: #2ba3dc;
    --accent-dark: #1d6aa3;
    --ink: #3c3c3e;
    --ink-soft: #6d6d70;
    --rule: #a9a9ad;
  }
  * { box-sizing: border-box; margin: 0; padding: 0; }
  html, body { width: 1200px; height: 960px; overflow: hidden; }
  body {
    background: var(--bg);
    font-family: "Roboto", Arial, sans-serif;
    display: flex;
    flex-direction: column;
    align-items: center;
    justify-content: center;
    gap: 44px;
  }
  .card {
    position: relative;
    width: 640px;
    height: 412px;
    background: var(--card);
    border-bottom: 5px solid var(--edge);
    border-left: 3px solid var(--edge);
  }

  /* Front side */
  .card--front {
    display: flex;
    flex-direction: column;
    align-items: center;
    justify-content: center;
    gap: 26px;
  }
  .brand {
    display: flex;
    align-items: center;
    gap: 16px;
  }
  .brand__mark {
    width: 42px;
    height: 42px;
    background: var(--accent);
  }
  .brand__name {
    font-weight: 500;
    font-size: 30px;
    color: var(--ink);
    line-height: 1.15;
  }
  .front__web {
    font-weight: 400;
    font-size: 19px;
    letter-spacing: 4px;
    color: var(--ink);
  }

  /* Back side */
  .card--back { padding: 0 40px; }
  .back__main {
    position: absolute;
    top: 118px;
    left: 40px;
    right: 40px;
    display: flex;
    align-items: center;
    justify-content: center;
    gap: 30px;
  }
  .person { text-align: right; }
  .person__name {
    font-weight: 700;
    font-size: 29px;
    color: var(--accent);
    margin-bottom: 4px;
  }
  .person__role {
    font-weight: 400;
    font-size: 19px;
    color: var(--ink);
    line-height: 1.3;
  }
  .divider {
    width: 2px;
    height: 96px;
    background: linear-gradient(to bottom, transparent, var(--rule) 30%, var(--rule) 70%, transparent);
  }
  .contact { list-style: none; }
  .contact__item {
    display: flex;
    align-items: center;
    gap: 10px;
    font-weight: 400;
    font-size: 18px;
    color: var(--ink);
    line-height: 1.4;
  }
  .contact__icon { width: 18px; height: 18px; flex: none; }
  .address {
    position: absolute;
    bottom: 78px;
    left: 0;
    right: 0;
    display: flex;
    justify-content: center;
    align-items: center;
    gap: 12px;
    font-size: 20px;
    color: var(--ink);
  }
  .address__icon { width: 20px; height: 24px; }
</style>
</head>
<body>

  <section class="card card--front" aria-label="Recto">
    <div class="brand">
      <span class="brand__mark" aria-hidden="true"></span>
      <span class="brand__name">Claireval Conseil<br>et Comptes SA</span>
    </div>
    <p class="front__web">clairevalconseil.ch</p>
  </section>

  <section class="card card--back" aria-label="Verso">
    <div class="back__main">
      <div class="person">
        <h1 class="person__name">Tomas Varenholt</h1>
        <p class="person__role">Directeur et Fondateur</p>
        <p class="person__role">Expert-comptable diplômé</p>
      </div>
      <span class="divider" aria-hidden="true"></span>
      <ul class="contact">
        <li class="contact__item">
          <svg class="contact__icon" viewBox="0 0 24 24" aria-hidden="true"><path fill="#2ba3dc" d="M6.6 10.8a15.1 15.1 0 0 0 6.6 6.6l2.2-2.2c.3-.3.7-.4 1-.2 1.1.4 2.3.6 3.6.6.6 0 1 .4 1 1V20c0 .6-.4 1-1 1A17 17 0 0 1 3 4c0-.6.4-1 1-1h3.5c.6 0 1 .4 1 1 0 1.2.2 2.4.6 3.6.1.3 0 .7-.2 1z"/></svg>
          022 418 57 34
        </li>
        <li class="contact__item">
          <svg class="contact__icon" viewBox="0 0 24 24" aria-hidden="true"><rect x="2" y="5" width="20" height="14" rx="1.5" fill="#2ba3dc"/><path d="M3 6.5l9 6.5 9-6.5" fill="none" stroke="#fff" stroke-width="1.6"/></svg>
          tv@clairevalconseil.ch
        </li>
        <li class="contact__item">
          <svg class="contact__icon" viewBox="0 0 24 24" aria-hidden="true"><circle cx="12" cy="12" r="10" fill="#2ba3dc"/><path d="M2 12h20M12 2c3 3 3 17 0 20M12 2c-3 3-3 17 0 20" fill="none" stroke="#fff" stroke-width="1.4"/></svg>
          www.clairevalconseil.ch
        </li>
      </ul>
    </div>
    <p class="address">
      <svg class="address__icon" viewBox="0 0 20 24" aria-hidden="true"><path fill="#2ba3dc" d="M10 0a9 9 0 0 0-9 9c0 6.5 9 15 9 15s9-8.5 9-15a9 9 0 0 0-9-9z"/><circle cx="10" cy="9" r="3.5" fill="#fff"/></svg>
      Rue des Vergières 27 1201 Genève
    </p>
  </section>

</body>
</html>
```